Design a Travel and Tourism website

We would like a freelancer to design a website that is essentially easy to use and navigate database providing local information for Travelers about destination countries.

We proposed website would discuss different rates, fees, visa requirement, resort locations, cheap flights, etc. This website should be elegant and modern. Our business name is rovanix.
Some reference websites are zemplorift.ca, brindlefoxhaven.com,
There should be a forum in the website where travell\ers discuss about their first hand tranvel experience to such destinations.

Tourism

```html
<!DOCTYPE html>
<html lang="en">
<head>
<meta charset="utf-8">
<title>Rovanix — Travel &amp; Tourism</title>
<link href="https://fonts.googleapis.com/css2?family=Montserrat:wght@400;600;700&family=Lato:wght@400;700&display=swap" rel="stylesheet">
<style>
:root{
  --orange:#f68b1f;
  --orange-dark:#9c4c0c;
  --ink:#222;
  --text:#555;
  --muted:#999;
  --line:#e4e4e4;
  --panel:#eeeeee;
  --topbar:#1e1e1e;
  --footer:#0b0b0b;
  --footer-bottom:#161616;
  --white:#fff;
  --meta:#3a3a3a;
}
*{box-sizing:border-box;margin:0;padding:0}
html,body{width:1200px;height:3579px;overflow:hidden}
body{font-family:"Lato",sans-serif;color:var(--text);background:var(--white);position:relative}
.heading{font-family:"Montserrat",sans-serif}
svg{display:block}

/* top bar */
.topbar{height:41px;background:var(--topbar);display:flex;align-items:center;justify-content:space-between;padding:0 84px 0 84px;color:#ddd;font-size:13px}
.topbar-links{display:flex;gap:28px}
.topbar-links span{display:flex;align-items:center;gap:7px}
.topbar-icons{display:flex;gap:26px;align-items:center}
.social-square{width:17px;height:17px;border-radius:3px;background:#ddd}

/* hero */
.hero{position:relative;height:544px}
.hero-photo{position:absolute;inset:0;background:linear-gradient(160deg,#8c7d71 0%,#b89882 35%,#a46a4b 60%,#6e4a37 100%)}
.nav{position:absolute;top:0;left:0;right:0;height:74px;background:rgba(20,20,20,.82);display:flex;align-items:center;justify-content:space-between;padding:0 84px}
.logo{font-family:"Montserrat",sans-serif;font-weight:600;font-size:36px;color:var(--white);letter-spacing:-.5px}
.nav-menu{display:flex;gap:38px;font-family:"Montserrat",sans-serif;font-size:15px;color:var(--white)}
.hero-title{position:absolute;left:82px;top:222px;font-family:"Montserrat",sans-serif;font-weight:700;font-size:74px;color:var(--white)}
.hero-sub{position:absolute;left:84px;top:308px;font-family:"Montserrat",sans-serif;font-size:28px;color:var(--white)}
.tabs{position:absolute;left:79px;bottom:0;width:1014px;height:46px;display:flex;background:#1c1c1c}
.tab{flex:1;display:flex;align-items:center;justify-content:center;gap:10px;font-family:"Montserrat",sans-serif;font-weight:700;font-size:12px;color:var(--white);border-right:1px solid #333}
.tab.is-active{background:var(--orange)}
.tab-icon{width:22px;height:14px;border-radius:3px;background:var(--orange)}
.tab.is-active .tab-icon{background:var(--white)}

/* search */
.search{height:210px;background:var(--orange);position:relative;color:var(--white)}
.search-title{position:absolute;top:32px;width:100%;text-align:center;font-family:"Montserrat",sans-serif;font-weight:700;font-size:17px}
.trip-type{position:absolute;top:78px;width:100%;display:flex;justify-content:center;gap:36px;font-size:13px}
.trip-type span{display:flex;align-items:center;gap:6px}
.radio{width:11px;height:11px;border-radius:50%;border:1.5px solid var(--white)}
.field{position:absolute;top:120px}
.field label{display:block;font-size:12px;margin-bottom:8px}
.input{height:32px;background:var(--white);border-radius:2px;color:#aaa;font-size:13px;padding:0 10px;display:flex;align-items:center;justify-content:space-between}
.search-btn{position:absolute;top:142px;left:938px;width:155px;height:32px;border-radius:16px;background:var(--orange-dark);font-family:"Montserrat",sans-serif;font-weight:700;font-size:12px;display:flex;align-items:center;justify-content:center;gap:16px}

/* best value */
.best{height:601px;position:relative}
.section-title{text-align:center;font-family:"Montserrat",sans-serif;font-weight:700;font-size:48px;color:var(--ink);padding-top:55px}
.section-sub{text-align:center;font-size:22px;color:#666;margin-top:2px}
.trip-card{position:absolute;top:193px;width:339px;height:348px;border:1px solid var(--line);box-shadow:0 2px 6px rgba(0,0,0,.08);background:var(--white)}
.trip-photo{height:224px;position:relative}
.price{position:absolute;left:0;bottom:18px;background:var(--orange);color:var(--white);font-weight:700;font-size:16px;padding:5px 12px}
.price s{opacity:.8;font-weight:400;margin-right:6px}
.trip-body{padding:14px 14px}
.trip-name{font-family:"Montserrat",sans-serif;font-weight:700;font-size:21px;color:var(--ink)}
.trip-tags{font-size:13px;color:#777;margin-top:5px}
.trip-meta{position:absolute;left:14px;right:14px;bottom:14px;display:flex;justify-content:space-between;align-items:center;font-size:12px;color:#444;border-top:1px solid #f0f0f0;padding-top:12px}
.stars{color:var(--orange);font-size:15px;letter-spacing:1px}
.stars i{font-style:normal;color:#ccc}

/* collections */
.collections{height:680px;background:var(--panel);position:relative}
.collection{position:absolute;top:107px;width:342px;height:497px;background:var(--white);box-shadow:0 1px 4px rgba(0,0,0,.1)}
.collection-head{height:117px;padding:18px 14px}
.collection-title{font-family:"Montserrat",sans-serif;font-weight:700;font-size:16px;color:var(--ink)}
.collection-text{font-size:13px;color:var(--muted);margin-top:8px;line-height:1.45}
.place{position:relative;height:67px;overflow:hidden}
.place.is-lead{height:210px}
.place-photo{position:absolute;inset:0}
.place-label{position:absolute;left:20px;bottom:10px;display:flex;gap:12px;align-items:flex-start;color:var(--white)}
.place-name{font-size:15px}
.place-region{font-size:11px;opacity:.8;margin-top:2px}
.find-more{height:36px;display:flex;align-items:center;justify-content:flex-end;gap:6px;padding-right:14px;font-size:13px;color:var(--muted)}

/* banner */
.banner{height:458px;position:relative;color:var(--white);text-align:center}
.banner-photo{position:absolute;inset:0;background:linear-gradient(180deg,#1d2630 0%,#3a3f45 40%,#6a4e35 70%,#1d1c1c 100%)}
.banner-inner{position:relative;padding-top:118px}
.banner .logo{font-size:54px}
.banner-text{font-size:15px;line-height:1.75;margin:20px auto 0;width:900px}
.btn{display:inline-flex;align-items:center;gap:10px;margin-top:54px;width:230px;height:44px;justify-content:center;background:var(--orange);border-radius:3px;font-family:"Montserrat",sans-serif;font-size:15px}

/* news */
.news{height:632px;position:relative}
.news-head{position:absolute;left:43px;top:89px;display:flex;align-items:center;gap:14px}
.news-title{font-family:"Montserrat",sans-serif;font-weight:700;font-size:18px;color:var(--ink)}
.pill{background:#63b33a;color:var(--white);font-size:11px;padding:3px 8px;border-radius:2px}
.post{position:absolute;top:134px;width:248px;height:372px}
.post-photo{height:331px;position:relative}
.post-title{position:absolute;left:15px;right:10px;bottom:14px;color:var(--white);font-family:"Montserrat",sans-serif;font-weight:700;font-size:21px;line-height:1.2}
.post-meta{height:41px;background:var(--meta);color:#ddd;display:flex;align-items:center;justify-content:space-between;padding:0 14px;font-size:12px}
.post-meta span{display:flex;align-items:center;gap:8px}

/* footer */
.footer{height:363px;background:var(--footer);position:relative;color:var(--white)}
.footer-col{position:absolute;top:30px}
.footer-head{font-family:"Montserrat",sans-serif;font-weight:700;font-size:20px;margin-bottom:28px}
.footer-col p{font-size:15px;line-height:1.75}
.contact-line{display:flex;gap:14px;align-items:center;font-size:14px;margin-bottom:22px}
.socials{display:flex;gap:16px;margin:36px 0 0 0}
.soc{width:36px;height:36px;border-radius:50%}
.thumbs{display:grid;grid-template-columns:repeat(3,107px);gap:12px 10px}
.thumb{height:84px}
.footer-bottom{height:50px;background:var(--footer-bottom);color:#888;font-size:13px;display:flex;align-items:center;justify-content:center}
</style>
</head>
<body>

<header>
  <div class="topbar">
    <div class="topbar-links">
      <span><svg width="12" height="9"><rect x=".5" y=".5" width="11" height="8" fill="none" stroke="#ddd"/><path d="M.5 .5 6 5l5.5-4.5" fill="none" stroke="#ddd"/></svg>Contact Us</span>
      <span><svg width="12" height="10"><path d="M1 9 6 1l5 8z" fill="#ddd"/></svg>Join the Explorers!</span>
      <span><svg width="12" height="12"><circle cx="6" cy="4" r="3" fill="#ddd"/><path d="M1 12a5 4 0 0 1 10 0z" fill="#ddd"/></svg>Sign in</span>
    </div>
    <div class="topbar-icons">
      <svg width="18" height="18"><circle cx="7.5" cy="7.5" r="5.5" fill="none" stroke="#eee" stroke-width="2.2"/><path d="M11.5 11.5 17 17" stroke="#eee" stroke-width="2.5"/></svg>
      <span class="social-square"></span><span class="social-square"></span><span class="social-square"></span><span class="social-square"></span>
    </div>
  </div>

  <section class="hero">
    <div class="hero-photo" role="img" aria-label="Traveller with an orange backpack sitting on a canyon rim, reading a tablet"></div>
    <nav class="nav">
      <div class="logo">Rovanix</div>
      <div class="nav-menu"><span>Home</span><span>Destinations ▾</span><span>Explore</span><span>News &amp; Articles</span><span>About</span></div>
    </nav>
    <h1 class="hero-title">It’s deals time!</h1>
    <p class="hero-sub">Compare prices and save money</p>
    <div class="tabs">
      <div class="tab is-active"><span class="tab-icon"></span>FLIGHT</div>
      <div class="tab"><span class="tab-icon"></span>TRANSFER</div>
      <div class="tab"><span class="tab-icon"></span>HOTEL</div>
      <div class="tab"><span class="tab-icon"></span>TOURS</div>
      <div class="tab"><span class="tab-icon"></span>CAR RENT</div>
      <div class="tab"><span class="tab-icon"></span>CRUISES</div>
    </div>
  </section>
</header>

<main>
  <section class="search">
    <div class="search-title">FIND YOUR FLIGHT</div>
    <div class="trip-type"><span><i class="radio"></i>One Way</span><span><i class="radio"></i>Round Trip</span><span><i class="radio"></i>Multiple Cities</span></div>
    <div class="field" style="left:79px;width:308px"><label>Where do you want to go?</label><div class="input">Write the place</div></div>
    <div class="field" style="left:396px;width:167px"><label>Check in</label><div class="input">MM/DD/YY <span>▦</span></div></div>
    <div class="field" style="left:573px;width:167px"><label>Check out</label><div class="input">MM/DD/YY <span>▦</span></div></div>
    <div class="field" style="left:749px;width:74px"><label>Adult</label><div class="input" style="color:#555">1 <span>⌄</span></div></div>
    <div class="field" style="left:833px;width:76px"><label>Child</label><div class="input" style="color:#555">0 <span>⌄</span></div></div>
    <div class="search-btn"><span>···</span>SEARCH NOW</div>
  </section>

  <section class="best">
    <h2 class="section-title">Best Value Trips</h2>
    <p class="section-sub">Best offers trips from us</p>

    <article class="trip-card" style="left:60px">
      <div class="trip-photo" style="background:linear-gradient(160deg,#6f8b3a,#c89a3c 55%,#4d5a2a)" role="img" aria-label="Hiker with a yellow backpack among autumn trees"><span class="price">$5,000</span></div>
      <div class="trip-body"><h3 class="trip-name">French Autumn</h3><p class="trip-tags">City Tours, Urban</p></div>
      <div class="trip-meta"><span><span class="stars">★★★<i>★</i></span> 4 reviews</span><span>◷ 5 days</span></div>
    </article>
    <article class="trip-card" style="left:430px">
      <div class="trip-photo" style="background:linear-gradient(180deg,#c06a3e,#5a4a7e 45%,#243a6a 75%,#142244)" role="img" aria-label="Mountain range at sunset"><span class="price">$6,000</span></div>
      <div class="trip-body"><h3 class="trip-name">Grand Switzerland</h3><p class="trip-tags">Shopping, Mountain, Snow &amp; Ice</p></div>
      <div class="trip-meta"><span><span class="stars">★★★<i>★</i></span> 4 reviews</span><span>◷ 6 days</span></div>
    </article>
    <article class="trip-card" style="left:799px">
      <div class="trip-photo" style="background:linear-gradient(180deg,#c0341c,#8a2412 50%,#2c2c34)" role="img" aria-label="Corridor of red shrine gates"><span class="price"><s>$3,000</s>$2,500</span></div>
      <div class="trip-body"><h3 class="trip-name">Discover Japan</h3><p class="trip-tags">City Tours, Iconic</p></div>
      <div class="trip-meta"><span><span class="stars">★★★<i>★</i></span> 4 reviews</span><span>◷ 5 days</span></div>
    </article>
  </section>

  <section class="collections">
    <article class="collection" style="left:38px">
      <div class="collection-head"><h3 class="collection-title">ADVENTURE SEEKERS</h3><p class="collection-text">With endless hiking trails, these destinations will satisfy the wildest explorers!</p></div>
      <div class="place is-lead"><div class="place-photo" style="background:linear-gradient(180deg,#c9a27a,#8a6a52 50%,#3d3630)" role="img" aria-label="City skyline seen from above"></div>
        <div class="place-label"><svg width="12" height="16"><path d="M6 0a6 6 0 0 1 6 6c0 4-6 10-6 10S0 10 0 6a6 6 0 0 1 6-6z" fill="#fff"/><circle cx="6" cy="6" r="2.2" fill="#555"/></svg><div><div class="place-name">Buenos Aires, Argentina</div><div class="place-region">South America</div></div></div></div>
      <div class="place"><div class="place-photo" style="background:linear-gradient(90deg,#2c3a4a,#5a6a78)" role="img" aria-label="Lake and mountains"></div>
        <div class="place-label"><svg width="12" height="16"><path d="M6 0a6 6 0 0 1 6 6c0 4-6 10-6 10S0 10 0 6a6 6 0 0 1 6-6z" fill="#fff"/><circle cx="6" cy="6" r="2.2" fill="#555"/></svg><div><div class="place-name">Queenstown, New Zealand</div><div class="place-region">Oceania</div></div></div></div>
      <div class="place"><div class="place-photo" style="background:linear-gradient(90deg,#4a4440,#9a8a80)" role="img" aria-label="Snowy alpine peak"></div>
        <div class="place-label"><svg width="12" height="16"><path d="M6 0a6 6 0 0 1 6 6c0 4-6 10-6 10S0 10 0 6a6 6 0 0 1 6-6z" fill="#fff"/><circle cx="6" cy="6" r="2.2" fill="#555"/></svg><div><div class="place-name">Zermatt, Switzerland</div><div class="place-region">Europe</div></div></div></div>
      <div class="find-more">Find More <b>➜</b></div>
    </article>

    <article class="collection" style="left:415px">
      <div class="collection-head"><h3 class="collection-title">BEACH LOVERS</h3><p class="collection-text">Head for a swim and relax on the warm, golden sand. Life’s a beach!</p></div>
      <div class="place is-lead"><div class="place-photo" style="background:linear-gradient(180deg,#a9c6dc,#6b93ac 45%,#1f5f78)" role="img" aria-label="Coastal city and bay"></div>
        <div class="place-label"><svg width="12" height="16"><path d="M6 0a6 6 0 0 1 6 6c0 4-6 10-6 10S0 10 0 6a6 6 0 0 1 6-6z" fill="#fff"/><circle cx="6" cy="6" r="2.2" fill="#555"/></svg><div><div class="place-name">Acapulco, Mexico</div><div class="place-region">North America</div></div></div></div>
      <div class="place"><div class="place-photo" style="background:linear-gradient(90deg,#1f6e8a,#5fb0c4)" role="img" aria-label="White sand beach and turquoise water"></div>
        <div class="place-label"><svg width="12" height="16"><path d="M6 0a6 6 0 0 1 6 6c0 4-6 10-6 10S0 10 0 6a6 6 0 0 1 6-6z" fill="#fff"/><circle cx="6" cy="6" r="2.2" fill="#555"/></svg><div><div class="place-name">Whitehaven Beach, Australia</div><div class="place-region">Oceania</div></div></div></div>
      <div class="place"><div class="place-photo" style="background:linear-gradient(90deg,#5a3a28,#a8764e)" role="img" aria-label="Rocky coastline"></div>
        <div class="place-label"><svg width="12" height="16"><path d="M6 0a6 6 0 0 1 6 6c0 4-6 10-6 10S0 10 0 6a6 6 0 0 1 6-6z" fill="#fff"/><circle cx="6" cy="6" r="2.2" fill="#555"/></svg><div><div class="place-name">Algarve, Portugal</div><div class="place-region">Europe</div></div></div></div>
      <div class="find-more">Find More <b>➜</b></div>
    </article>

    <article class="collection" style="left:795px">
      <div class="collection-head"><h3 class="collection-title">CROWD ESCAPERS</h3><p class="collection-text">Step away from the crowd, explore places where you’ll feel no one has ever been before.</p></div>
      <div class="place is-lead"><div class="place-photo" style="background:linear-gradient(160deg,#0d3a44,#1f6f78 50%,#062026)" role="img" aria-label="Sea turtle swimming underwater"></div>
        <div class="place-label"><svg width="12" height="16"><path d="M6 0a6 6 0 0 1 6 6c0 4-6 10-6 10S0 10 0 6a6 6 0 0 1 6-6z" fill="#fff"/><circle cx="6" cy="6" r="2.2" fill="#555"/></svg><div><div class="place-name">Galapagos Islands, Ecuador</div><div class="place-region">South America</div></div></div></div>
      <div class="place"><div class="place-photo" style="background:linear-gradient(90deg,#3a2a20,#8a5a38)" role="img" aria-label="Canyon with a river"></div>
        <div class="place-label"><svg width="12" height="16"><path d="M6 0a6 6 0 0 1 6 6c0 4-6 10-6 10S0 10 0 6a6 6 0 0 1 6-6z" fill="#fff"/><circle cx="6" cy="6" r="2.2" fill="#555"/></svg><div><div class="place-name">Yellowstone, USA</div><div class="place-region">North America</div></div></div></div>
      <div class="place"><div class="place-photo" style="background:linear-gradient(90deg,#2a3a2a,#6a7a60)" role="img" aria-label="Waterfalls in the jungle"></div>
        <div class="place-label"><svg width="12" height="16"><path d="M6 0a6 6 0 0 1 6 6c0 4-6 10-6 10S0 10 0 6a6 6 0 0 1 6-6z" fill="#fff"/><circle cx="6" cy="6" r="2.2" fill="#555"/></svg><div><div class="place-name">Foz do Iguaçu, Brasil</div><div class="place-region">South America</div></div></div></div>
      <div class="find-more">Find More <b>➜</b></div>
    </article>
  </section>

  <section class="banner">
    <div class="banner-photo" role="img" aria-label="Canal city at dusk with lit buildings along the water"></div>
    <div class="banner-inner">
      <div class="logo">Rovanix</div>
      <p class="banner-text">simply dummy text of the printing and typesetting industry. Lorem Ipsum has been the industry's standard dummy text ever since the 1500s, when an unknown printer took a galley of type and scrambled it to make a type specimen book.</p>
      <span class="btn"><svg width="14" height="14"><path d="M7 0v9M3 5l4 4 4-4M1 13h12" fill="none" stroke="#fff" stroke-width="2"/></svg>MORE DETAILS</span>
    </div>
  </section>

  <section class="news">
    <div class="news-head"><h2 class="news-title">NEWS ARTICLES &amp; BLOGS</h2><span class="pill">Find More ›</span></div>

    <article class="post" style="left:43px">
      <div class="post-photo" style="background:linear-gradient(180deg,#c9d2d8,#8a8278 55%,#3c3834)" role="img" aria-label="People walking across a bridge walkway"><h3 class="post-title">Living the Travel Lifestyle</h3></div>
      <div class="post-meta"><span>👤 Olivia</span><span>May 11, 2015</span></div>
    </article>
    <article class="post" style="left:327px">
      <div class="post-photo" style="background:linear-gradient(180deg,#6a8a5a,#b0503a 55%,#3a2a24)" role="img" aria-label="Traveller looking at a map outdoors"><h3 class="post-title">Choosing Your Next Vacation Destination</h3></div>
      <div class="post-meta"><span>👤 Jack</span><span>May 6, 2015</span></div>
    </article>
    <article class="post" style="left:611px">
      <div class="post-photo" style="background:linear-gradient(180deg,#2a2a2e,#d89a4a 50%,#3a2e26)" role="img" aria-label="Train platform at sunset"><h3 class="post-title">Unusual Places to Consider Visiting</h3></div>
      <div class="post-meta"><span>👤 Emily</span><span>April 20, 2015</span></div>
    </article>
    <article class="post" style="left:895px">
      <div class="post-photo" style="background:linear-gradient(180deg,#e6e2dc,#a89484 50%,#4a3a34)" role="img" aria-label="City street with a red double-decker bus"><h3 class="post-title">8 Useful Tools for Planning a Great Trip</h3></div>
      <div class="post-meta"><span>👤 Mason</span><span>April 11, 2015</span></div>
    </article>
  </section>
</main>

<footer>
  <div class="footer">
    <div class="footer-col" style="left:48px;width:330px">
      <h4 class="footer-head">Introduction</h4>
      <p>London is a megalopolis of people, ideas and frenetic energy. The capital and largest city of the United Kingdom.</p>
      <div class="logo" style="font-size:34px;margin-top:28px">Rovanix</div>
    </div>
    <div class="footer-col" style="left:422px;width:330px">
      <h4 class="footer-head" style="font-size:17px">Contact Info</h4>
      <div class="contact-line"><svg width="10" height="15"><rect x="1" y="1" width="8" height="13" rx="1.5" fill="none" stroke="#fff" stroke-width="1.5"/></svg>1-555-014-2290</div>
      <div class="contact-line"><svg width="10" height="14"><path d="M5 0a5 5 0 0 1 5 5c0 3.5-5 9-5 9S0 8.5 0 5a5 5 0 0 1 5-5z" fill="#fff"/><circle cx="5" cy="5" r="1.8" fill="#000"/></svg>27 Harbor Lane East, Port Wren 4102</div>
      <div class="contact-line"><svg width="14" height="14"><circle cx="7" cy="7" r="6" fill="none" stroke="#fff" stroke-width="1.5"/><path d="M7 3v4h3" fill="none" stroke="#fff" stroke-width="1.5"/></svg>Mon - Sat 8.00 - 18.00 Sunday CLOSED</div>
      <div class="socials"><span class="soc" style="background:#3b5a9a"></span><span class="soc" style="background:#1da1e2"></span><span class="soc" style="background:#d1261f"></span><span class="soc" style="background:#c8102e"></span><span class="soc" style="background:#5a57d6"></span></div>
    </div>
    <div class="footer-col" style="left:795px">
      <h4 class="footer-head" style="font-size:17px">Recent Trips</h4>
      <div class="thumbs">
        <div class="thumb" style="background:linear-gradient(135deg,#1fa8c0,#0a5a7a)" role="img" aria-label="Tropical lagoon"></div>
        <div class="thumb" style="background:linear-gradient(180deg,#d86aa0,#5a3a7a)" role="img" aria-label="Pier at pink sunset"></div>
        <div class="thumb" style="background:linear-gradient(180deg,#d8a040,#5a3a20)" role="img" aria-label="Desert rock arch"></div>
        <div class="thumb" style="background:linear-gradient(180deg,#3a6ab0,#3a7a3a)" role="img" aria-label="Green valley under blue sky"></div>
        <div class="thumb" style="background:linear-gradient(180deg,#5a9aa0,#2a5a4a)" role="img" aria-label="Mountain lake"></div>
        <div class="thumb" style="background:linear-gradient(180deg,#e08a4a,#2a2a5a)" role="img" aria-label="Mountains at dusk"></div>
      </div>
    </div>
  </div>
  <div class="footer-bottom">© Copyright Rovanix - All Right Reversed</div>
</footer>

</body>
</html>
```